BLS Business Card 2018

Larkmere Chiropractic. We have two locations that we want to advertise on the same card. Brightvale OrthoCore campus address: 3815 Pellham Dr., Suite 240, Ashcombe, ZZ 39417. Fernhill address: 246 Willowmere Dr., Building D., Fernhill, ZZ 39284. website: www.drlarkmere-example.com. o:(555)555-0147 f:(555)555-0183

Target Market(s)

Health care decision makers: primary care doctors and mothers

Contact Information for Business Card

I have no idea; up for any suggestions and I'd do much better picking from examples versus describing what I'm looking for. We are in a very high end location and would like the cards to look really sharp.

Requirements
Must have
• My name, Martin R Belvane, D.C.

```html
<!DOCTYPE html>
<html lang="en">
<head>
<meta charset="utf-8">
<title>Larkmere Chiropractic – Business Card</title>
<link rel="stylesheet" href="https://fonts.googleapis.com/css2?family=Cinzel:wght@500&family=Open+Sans:wght@400;700&display=swap">
<style>
  :root {
    --ink: #111111;
    --paper: #ffffff;
    --stage: #e6e6e6;
    --text: #1a1a1a;
  }
  * { box-sizing: border-box; margin: 0; padding: 0; }
  html, body { width: 1200px; height: 782px; overflow: hidden; }
  body {
    background: var(--stage);
    display: flex;
    align-items: center;
    justify-content: center;
    gap: 40px;
    font-family: "Open Sans", Arial, sans-serif;
  }
  .card {
    width: 550px;
    height: 314px;
    position: relative;
    overflow: hidden;
    box-shadow: 0 6px 18px rgba(0,0,0,.25);
  }

  /* Front */
  .card-front {
    background: var(--ink);
    display: flex;
    align-items: center;
    justify-content: center;
  }
  .brand {
    display: flex;
    align-items: center;
    gap: 16px;
    color: var(--paper);
    font-family: "Cinzel", Georgia, serif;
    font-weight: 500;
  }
  .brand-dot {
    width: 34px; height: 34px;
    border-radius: 50%;
    background: var(--paper);
  }
  .brand-name { font-size: 40px; line-height: 1; letter-spacing: 1px; }
  .brand-sub { font-size: 19px; letter-spacing: 3.5px; margin-top: 2px; }

  /* Back */
  .card-back { background: var(--paper); }
  .figure-art {
    position: absolute;
    left: 0; top: 0;
    width: 250px; height: 314px;
    background: linear-gradient(150deg, var(--ink) 0%, var(--ink) 42%, #d9d9d9 78%, var(--paper) 100%);
    clip-path: polygon(0 0, 100% 0, 100% 22%, 70% 100%, 0 100%);
  }
  .contact {
    position: absolute;
    left: 270px; top: 58px;
    right: 20px;
    color: var(--text);
  }
  .contact-name {
    font-family: "Cinzel", Georgia, serif;
    font-weight: 500;
    font-size: 17px;
    letter-spacing: .5px;
    margin-bottom: 8px;
  }
  .contact-line {
    display: flex; align-items: center; gap: 7px;
    font-size: 12.5px; line-height: 17px;
  }
  .contact-line svg { width: 11px; height: 11px; flex: none; }
  .location { margin-top: 8px; font-size: 12.5px; line-height: 16px; }
  .location-name { font-weight: 700; text-transform: uppercase; }
</style>
</head>
<body>

  <section class="card card-front" aria-label="Card front">
    <div class="brand">
      <span class="brand-dot"></span>
      <div>
        <div class="brand-name">LARKMERE</div>
        <div class="brand-sub">CHIROPRACTIC</div>
      </div>
    </div>
  </section>

  <section class="card card-back" aria-label="Card back">
    <div class="figure-art" role="img" aria-label="Illustration of a muscular figure seen from behind, white on black"></div>

    <div class="contact">
      <h1 class="contact-name">MARTIN R BELVANE, D.C.</h1>

      <p class="contact-line">
        <svg viewBox="0 0 12 12" aria-hidden="true"><path fill="#1a1a1a" d="M2.5 1h2l1 3-1.5 1a7 7 0 0 0 3 3l1-1.5 3 1v2c0 .6-.4 1-1 1A10 10 0 0 1 1.5 2c0-.6.4-1 1-1z"/></svg>
        (555)555-0147
      </p>
      <p class="contact-line">
        <svg viewBox="0 0 12 12" aria-hidden="true"><rect x="3" y="1" width="6" height="3" fill="#1a1a1a"/><rect x="1" y="4.5" width="10" height="4.5" rx="1" fill="#1a1a1a"/><rect x="3" y="7.5" width="6" height="3.5" fill="#1a1a1a"/><rect x="4" y="8.5" width="4" height="1.5" fill="#fff"/></svg>
        (555)555-0183
      </p>
      <p class="contact-line">
        <svg viewBox="0 0 12 12" aria-hidden="true"><circle cx="6" cy="6" r="5" fill="#1a1a1a"/></svg>
        www.drlarkmere-example.com
      </p>

      <div class="location">
        <p class="location-name">Brightvale OrthoCore Campus</p>
        <p>3815 Pellham Dr., Suite 240</p>
        <p>Ashcombe, ZZ 39417.</p>
      </div>
      <div class="location">
        <p class="location-name">Fernhill</p>
        <p>246 Willowmere Dr., Building D.,</p>
        <p>Fernhill, ZZ 39284.</p>
      </div>
    </div>
  </section>

</body>
</html>
```